Corvel Capital LLC

Need Professional Business cards for New Investment Fund

Target Market(s)

High Quality investors

Industry/Entity Type

Financial

Contact Information for Business Card

Phone Number +1 555 284 6190
Name Lukas Varenko
Title Fund Manager
email lv@FundCorvel.com
Website www.FundCorvel.com

Colors

Designer to choose colors to be used in the design.

Requirements
Must have
• Must have our Logo and all of the above. Must be made so lettering and loge can be raised

```html
<!DOCTYPE html>
<html lang="en">
<head>
<meta charset="utf-8">
<title>Quenvar – Business Card</title>
<link rel="stylesheet" href="https://fonts.googleapis.com/css2?family=Montserrat:wght@600;700&family=Questrial&display=swap">
<style>
  :root {
    --backdrop: #161616;
    --card: #262626;
    --card-edge: #2e2e2e;
    --green: #2be41a;
    --white: #f2f2f2;
  }
  * { margin: 0; padding: 0; box-sizing: border-box; }
  html, body { width: 1200px; height: 900px; overflow: hidden; }
  body {
    background: radial-gradient(ellipse at 60% 40%, #232323 0%, var(--backdrop) 70%);
    font-family: "Questrial", "Century Gothic", sans-serif;
    color: var(--white);
    position: relative;
  }
  .card {
    position: absolute;
    left: 285px;
    width: 630px;
    height: 360px;
    background: linear-gradient(135deg, var(--card) 0%, var(--card-edge) 100%);
    border-bottom: 7px solid var(--green);
    box-shadow: 0 12px 30px rgba(0,0,0,0.55);
  }
  .card--front { top: 65px; }
  .card--back { top: 470px; }

  .wordmark {
    font-family: "Montserrat", sans-serif;
    font-weight: 700;
    color: var(--green);
    letter-spacing: 4px;
    display: flex;
    align-items: center;
    gap: 12px;
    white-space: nowrap;
  }
  .wordmark__dot {
    width: 16px; height: 16px;
    border-radius: 50%;
    background: var(--green);
    flex: none;
  }
  .card--front .wordmark {
    position: absolute;
    left: 0; right: 0; top: 0; bottom: 0;
    justify-content: center;
    font-size: 44px;
  }
  .card--back .wordmark {
    position: absolute;
    left: 40px; top: 150px;
    font-size: 36px;
  }

  .divider {
    position: absolute;
    left: 318px; top: 92px;
    width: 2px; height: 160px;
    background: var(--green);
  }

  .contact {
    position: absolute;
    left: 350px; top: 100px;
  }
  .contact__name {
    font-family: "Montserrat", sans-serif;
    font-weight: 700;
    font-size: 25px;
    color: var(--green);
    letter-spacing: 0.5px;
  }
  .contact__title {
    font-size: 19px;
    margin-top: 2px;
    margin-bottom: 22px;
  }
  .contact__line {
    display: flex;
    align-items: center;
    gap: 12px;
    font-size: 19px;
    letter-spacing: 0.5px;
    line-height: 31px;
  }
  .contact__icon { width: 15px; height: 15px; flex: none; }
  .accent { color: var(--green); }
</style>
</head>
<body>

  <section class="card card--front" aria-label="Card front">
    <div class="wordmark"><span class="wordmark__dot"></span>QUENVAR</div>
  </section>

  <section class="card card--back" aria-label="Card back">
    <div class="wordmark"><span class="wordmark__dot"></span>QUENVAR</div>
    <div class="divider"></div>
    <div class="contact">
      <p class="contact__name">Lukas Varenko</p>
      <p class="contact__title">Fund Manager</p>
      <p class="contact__line">
        <svg class="contact__icon" viewBox="0 0 16 16" aria-hidden="true"><path d="M4 1 L6.5 4.5 L5 6.5 Q6.5 9.5 9.5 11 L11.5 9.5 L15 12 L13 15 Q6 14 1 3 Z" fill="none" stroke="#2be41a" stroke-width="1.5" stroke-linejoin="round"/></svg>
        +1 555 284 6190
      </p>
      <p class="contact__line">
        <svg class="contact__icon" viewBox="0 0 16 16" aria-hidden="true"><rect x="1" y="3" width="14" height="10" fill="none" stroke="#2be41a" stroke-width="1.5"/><path d="M1 3 L8 9 L15 3" fill="none" stroke="#2be41a" stroke-width="1.5"/></svg>
        lv@FundCorvel.com
      </p>
      <p class="contact__line">
        <svg class="contact__icon" viewBox="0 0 16 16" aria-hidden="true"><circle cx="8" cy="8" r="7" fill="#2be41a"/><path d="M1 8 H15 M8 1 V15 M3 4 H13 M3 12 H13" stroke="#262626" stroke-width="1"/></svg>
        <span>www.<span class="accent">FundCorvel</span>.com</span>
      </p>
    </div>
  </section>

</body>
</html>
```